Wall art for an Investments Lab at a college

Wall art for inside a new investments lab. A photo of the lab is attached. The wall art will go on the wall in the back right (pictured). It is currently white and the adjacent walls are white. The accent wall in the room is blue (summer nights). A copy of our color palette for environmental design is also attached. The tag line should be INVESTING IN THE FUTURE.

Target Market(s)

College students

Industry/Entity Type

Finance

Requirements
Must have
• Incorporate colors from palette

```html
<!DOCTYPE html>
<html lang="en">
<head>
<meta charset="UTF-8">
<title>Investing in the Future – Wall Art</title>
<link rel="stylesheet" href="https://fonts.googleapis.com/css2?family=Allerta+Stencil&display=swap">
<style>
  :root {
    --summer-night-light: #5c8aab;
    --summer-night-mid: #3f7191;
    --summer-night-deep: #124e6d;
    --wave-light: rgba(170, 215, 240, 0.38);
    --wave-soft: rgba(170, 215, 240, 0);
    --frame-white: #ffffff;
  }

  html, body {
    margin: 0;
    padding: 0;
    overflow: hidden;
  }

  .wall-art {
    position: relative;
    width: 1200px;
    height: 928px;
    overflow: hidden;
    background: linear-gradient(90deg, var(--summer-night-light) 0%, var(--summer-night-mid) 55%, var(--summer-night-deep) 100%);
  }

  .wave-field {
    position: absolute;
    left: 0;
    top: 100px;
    width: 1200px;
    height: 680px;
    background:
      radial-gradient(ellipse 40% 35% at 62% 38%, var(--wave-light), var(--wave-soft) 70%),
      radial-gradient(ellipse 45% 30% at 25% 55%, var(--wave-light), var(--wave-soft) 70%),
      radial-gradient(ellipse 55% 22% at 70% 75%, var(--wave-light), var(--wave-soft) 70%);
  }

  .tagline-frame {
    position: absolute;
    left: 92px;
    top: 170px;
    width: 1007px;
    height: 147px;
    box-sizing: border-box;
    border: 6px solid var(--frame-white);
    display: flex;
    align-items: center;
    justify-content: center;
  }

  .tagline {
    margin: 0;
    color: var(--frame-white);
    font-family: "Allerta Stencil", sans-serif;
    font-weight: 400;
    font-size: 66px;
    line-height: 1;
    letter-spacing: 0.01em;
    text-transform: uppercase;
    white-space: nowrap;
  }
</style>
</head>
<body>
  <main class="wall-art">
    <div class="wave-field" role="img" aria-label="Flowing light-blue wireframe wave ribbons and looping line spirals sweeping across the wall"></div>
    <div class="tagline-frame">
      <h1 class="tagline">Investing in the Future.</h1>
    </div>
  </main>
</body>
</html>
```